Abia Investment Brochure for investment promotion

We need an investment manual to sell the potential of Kessara State (a state in Nigeria) to investors around the world. This manual / brochure should be top class and have a premium feel.

We have developed the content as attached and all that is required is to fit the content into a brochure format.
The brochure should be top class, easy to read and very friendly to investors

Target Market(s)

World Investors

Industry/Entity Type

Investment

Requirements
Must have
• Kessara State Logo (Can find online), Kessara Tower (can find online). Premium feel and look. design should be clean, no clutter. General images that represent investment sectors
Nice to have
• Pictures
Should not have
• Images of white men.

```html
<!DOCTYPE html>
<html lang="en">
<head>
<meta charset="utf-8">
<title>Industry Overview / Investment Opportunities</title>
<link href="https://fonts.googleapis.com/css2?family=Open+Sans:wght@400;600;700&display=swap" rel="stylesheet">
<style>
  :root{
    --band:#2f6b2c;
    --band-dark:#1f4f1e;
    --heading:#3f8f2a;
    --accent:#d8761e;
    --text:#2b2b2b;
    --page:#ffffff;
  }
  *{margin:0;padding:0;box-sizing:border-box}
  html,body{width:849px;height:1200px;overflow:hidden;background:var(--page)}
  body{font-family:"Open Sans",Arial,sans-serif;color:var(--text);font-size:10.6px;line-height:1.48;position:relative}
  .page-header{height:40px;background:linear-gradient(90deg,var(--band-dark),var(--band));color:#fff;display:flex;align-items:center;padding-left:34px;font-size:19px;font-weight:600;letter-spacing:.2px}
  .content{padding:16px 40px 0 34px}
  .section-title{color:var(--heading);font-size:14px;font-weight:700;margin:0 0 5px}
  p{margin:0 0 8px}
  ul{list-style:none;margin:0 0 14px}
  li{padding-left:14px;position:relative;margin-bottom:2px}
  li::before{content:"";position:absolute;left:2px;top:6px;width:4px;height:4px;background:var(--text);border-radius:50%}
  .highlight{color:var(--accent);font-weight:700}
  section{margin-bottom:10px}
  .photo-strip{position:absolute;left:0;right:0;bottom:0;height:196px;display:grid;grid-template-columns:1fr 1fr 1.25fr 1.6fr;grid-template-rows:1fr 1fr;gap:4px;background:#fff;padding-top:4px}
  .photo{display:block}
  .p1{grid-column:1;grid-row:1;background:linear-gradient(135deg,#7a8f5a,#c9b07a)}
  .p2{grid-column:2;grid-row:1;background:linear-gradient(135deg,#4d7a3a,#a9c27a)}
  .p3{grid-column:1/3;grid-row:2;background:linear-gradient(135deg,#5b6e3c,#b88a4e)}
  .p4{grid-column:3;grid-row:1/3;background:linear-gradient(160deg,#3f6a2f,#8fb26a)}
  .p5{grid-column:4;grid-row:1/3;background:linear-gradient(160deg,#6b8aa8,#c9d6c2 55%,#5a7a3c)}
</style>
</head>
<body>
  <header class="page-header">Industry Overview / Investment Opportunities</header>

  <main class="content">
    <section>
      <h2 class="section-title">Healthcare</h2>
      <p>Kessara has the vision to become a preferred destination for medical tourism in Nigeria and West African sub-region.</p>
      <p>Kessara State is known for the provision of technologically-driven special medical and healthcare services in priority areas such as cardiac catheterization, cancer treatment, medical transplants, neonatal intensive care, neurosurgery, fertility treatment, trauma care, etc. and supported by mobile emergency medical/healthcare services across the state.</p>
      <p>The government of Kessara is ready for partnerships with medical and healthcare management experts in all the following areas:</p>
      <ul>
        <li>Specialized Hospitals of world-class standards</li>
        <li>Upgrade with appropriate health infrastructure, build and maintain institutional capacity of existing tertiary, secondary and primary healthcare facilities to standard.</li>
        <li>Affordable and efficient formal and community health insurance schemes</li>
        <li>Ambulance services including air ambulance, motorcycle, bicycle, etc.</li>
        <li>Management of State-owned special healthcare training facilities and the teaching hospital.</li>
      </ul>
    </section>

    <section>
      <h2 class="section-title">Trade and commerce</h2>
      <p>The second most important economic engine in Kessara is Trade and Commerce. The largest market in West Africa, the Ameria market with over 100,000 shops and an estimated 50,000 shoppers daily is located in Oboro. Also in Oboro are four other markets with a total capacity of over 25,000 shops. This makes the state of Kessara the commercial hub of Nigeria and indeed West Africa. A significant number of Nigeria's blue-chip companies also have their manufacturing or major distribution hubs in Oboro.</p>
      <p>Oboro in the early 1980's was a host to a majority of medium and large scale manufacturing sites in Nigeria.The present government is putting everything in place to re-ignite the manufacturing potential of Oboro, once referred to as the Eyimba city, translated literally as the Elephant city.</p>
    </section>

    <section>
      <h2 class="section-title">Travel and Tourism</h2>
      <p>Kessara State is blessed with abundant potentials for a viable tourism industry. Some of the potential tourism potentials yet to be optimized include:</p>
      <p><span class="highlight">The Azeli Blue River:</span> The blueness and freshness of the river makes it unique. The river has room for the construction of a world-class tourism resort. If fully developed, the Azeli Blue River site can provide an all-year round income and a major destination point for leisure seekers worldwide.</p>
      <p><span class="highlight">The Long Juju of Arodeke:</span> An important historical site, this is a cave with a long dark tunnel that is associated with the slave trade era.</p>
      <p><span class="highlight">The National War Museum and Okeke Bunker in Umuleke:</span> These establishments contain the relics of the Nigerian Civil War.</p>
      <p>Tourism and Hospitality areas with high investment opportunity include;</p>
      <ul>
        <li>Development and Management of top class hotels</li>
        <li>Development of Theme Parks and Resorts</li>
        <li>Development of Entertainment Centres, Shopping Arcades and Malls</li>
      </ul>
    </section>
  </main>

  <div class="photo-strip">
    <div class="photo p1" role="img" aria-label="Photo of a busy open-air market"></div>
    <div class="photo p2" role="img" aria-label="Photo of green farmland and crops"></div>
    <div class="photo p3" role="img" aria-label="Photo of traders and goods at a market stall"></div>
    <div class="photo p4" role="img" aria-label="Photo of a lush tropical forest walkway"></div>
    <div class="photo p5" role="img" aria-label="Photo of a scenic river surrounded by greenery"></div>
  </div>
</body>
</html>
```